Organization and people consulting firm needs a website design

I need a website that promotes and explains the consulting service we will provide. The organization is called Bluefinch Advisory Partners. Our services include organization design, employee experience, change management, and executive coaching. I would like to see a simple clean and professional design, that reflects a modern and forward looking professional services company

Target Market(s)

Mid market and large companies

Industry/Entity Type

Management Consulting

Coding

Coded - Design and coding required

Number of Pages Required

5+ page

Font styles to use
Sans Serif

Colors

Designer to choose colors to be used in the design.

Requirements
Must have
• The following pages: Home, The Way We Work, What We Do, Our Founder, Insights, Contact.
• Search button.
• Hyper links (will be provided with main body text)
• Scrolling website with summaries at top level and links to more detail at lower level (like this website: veltracore.com)
• Company logo (uploaded)
• I have text for each of the pages that I can upload once the basic design is done
Should not have
• No clutter, keep the design clean

```html
<!DOCTYPE html>
<html lang="en">
<head>
<meta charset="utf-8">
<title>Bluefinch Advisory Partners</title>
<link href="https://fonts.googleapis.com/css2?family=Cinzel:wght@400;600&family=Lato:wght@400;700&family=Open+Sans:wght@400;600&display=swap" rel="stylesheet">
<style>
:root{
  --red:#e8232f;
  --ink:#555555;
  --muted:#9a9a9a;
  --white:#ffffff;
  --dark:#1f1f1f;
  --grey:#f1f1f1;
}
*{box-sizing:border-box;margin:0;padding:0}
html,body{width:1200px;height:3607px;overflow:hidden}
body{position:relative;background:var(--white);font-family:'Lato',sans-serif;color:var(--ink)}
.abs{position:absolute}
section{position:absolute;left:0;width:1200px}
.hero{top:0;height:556px;background:linear-gradient(160deg,#2c2c2c 0%,#141414 55%,#262626 100%)}
.hero-photo{position:absolute;inset:0;background:radial-gradient(ellipse at 55% 40%,rgba(90,90,90,.45),rgba(0,0,0,0) 60%)}
.brand{left:120px;top:32px;width:300px;font-family:'Cinzel',serif;font-size:24px;font-weight:400;color:var(--white);letter-spacing:2px;line-height:30px}
.search{left:996px;top:22px;width:87px;height:33px;background:var(--red);color:var(--white);font-size:15px;text-align:center;line-height:33px;text-transform:uppercase}
.nav{left:498px;top:72px;display:flex;gap:30px;font-family:'Open Sans',sans-serif;font-weight:600;font-size:14px;color:var(--white)}
.nav .active{color:var(--red)}
.hero-title{left:0;width:1200px;top:216px;text-align:center;font-family:'Cinzel',serif;font-size:44px;line-height:58px;color:var(--white)}
.btn{position:absolute;height:49px;line-height:49px;text-align:center;font-size:17px;text-transform:uppercase;letter-spacing:.3px}
.btn-white{background:var(--white);color:var(--red);box-shadow:0 2px 8px rgba(0,0,0,.18)}
.btn-red{background:var(--red);color:var(--white);box-shadow:0 2px 8px rgba(0,0,0,.18)}
.title{left:0;width:1200px;text-align:center;font-family:'Open Sans',sans-serif;font-size:40px;font-weight:600;color:#555}
.para{left:130px;width:940px;text-align:center;font-size:22px;line-height:36px;color:var(--muted)}
.way{top:556px;height:495px;background:var(--white)}
.what{top:1051px;height:770px;background:linear-gradient(125deg,#ededed 0%,#f6f6f6 45%,#e9e9e9 70%,#f3f3f3 100%)}
.founder{top:1821px;height:649px;background:linear-gradient(165deg,#ffffff 0%,#f7f7f7 60%,#ececec 100%)}
.insights{top:2470px;height:529px;background:linear-gradient(125deg,#ececec 0%,#f5f5f5 50%,#e6e6e6 100%)}
.contact{top:2999px;height:512px;background:linear-gradient(170deg,#ffffff 0%,#f8f8f8 70%,#efefef 100%)}
.service{position:absolute;width:200px;text-align:center}
.service svg{display:block;margin:0 auto}
.service-label{margin-top:14px;font-family:'Cinzel',serif;font-size:16px;line-height:24px;color:#555}
.photo{left:339px;top:339px;width:238px;height:199px;background:linear-gradient(90deg,#e6e2da 0%,#c9ccd4 45%,#8a7560 100%);box-shadow:0 3px 10px rgba(0,0,0,.3);border:3px solid #fff}
.founder-name{left:600px;width:310px;top:362px;text-align:center;font-family:'Open Sans',sans-serif;font-size:32px;font-weight:600;color:#444}
.founder-role{left:600px;width:310px;top:404px;text-align:center;font-family:'Open Sans',sans-serif;font-size:28px;color:#666}
.detail{position:absolute;display:flex;align-items:flex-start;gap:14px;font-size:15px;line-height:24px;color:#555}
.detail svg{flex:none}
.footer{top:3511px;height:96px;background:var(--dark)}
.foot-nav{left:118px;top:38px;display:flex;gap:26px;font-family:'Open Sans',sans-serif;font-weight:600;font-size:12px;color:var(--white)}
.copy{left:862px;top:38px;font-size:12px;color:#ccc}
</style>
</head>
<body>

<section class="hero">
  <div class="hero-photo" role="img" aria-label="Dark photograph of a business handshake across a desk"></div>
  <div class="abs brand">Bluefinch Advisory Partners</div>
  <div class="abs search">Search</div>
  <nav class="abs nav">
    <span class="active">Home</span><span>The Way We Work</span><span>What We Do</span><span>Our Founder</span><span>Insights</span><span>Contact</span>
  </nav>
  <h1 class="abs hero-title">We are organisation &amp; people<br>consulting firm</h1>
  <div class="btn btn-white" style="left:522px;top:378px;width:156px">Learn More</div>
</section>

<section class="way">
  <h2 class="abs title" style="top:100px">The Way We Work</h2>
  <p class="abs para" style="top:181px">Lorem ipsum dolor sit amet, consectetur adipiscing elit, sed do eiusmod tempor incidi dunt ut labore et dolore magna aliqua. Ut enim ad mainim veniam, quis nostrud exercitea tion ual lamco laboris nisi ut aliquip ex ea commodo consequat.</p>
  <div class="btn btn-red" style="left:522px;top:331px;width:156px">Learn More</div>
</section>

<section class="what">
  <h2 class="abs title" style="top:100px">What We Do</h2>
  <p class="abs para" style="top:182px">Lorem ipsum dolor sit amet, consectetur adipiscing elit, sed do eiusmod tempor incidi dunt ut labore et dolore magna aliqua. Ut enim ad mainim veniam, quis nostrud exercitea tion ual lamco laboris nisi ut aliquip ex ea commodo consequat.</p>

  <div class="service" style="left:148px;top:346px">
    <svg width="128" height="128" viewBox="0 0 128 128"><circle cx="64" cy="64" r="62" fill="none" stroke="var(--red)" stroke-width="2"/><circle cx="64" cy="64" r="54" fill="none" stroke="#e8a0a4" stroke-width="1"/><rect x="50" y="40" width="28" height="48" fill="none" stroke="var(--red)" stroke-width="3"/><path d="M56 52h16M56 62h16M56 72h16" stroke="var(--red)" stroke-width="3"/></svg>
    <div class="service-label">Organisation<br>Design</div>
  </div>
  <div class="service" style="left:381px;top:346px">
    <svg width="128" height="128" viewBox="0 0 128 128"><circle cx="64" cy="64" r="62" fill="none" stroke="var(--red)" stroke-width="2"/><circle cx="64" cy="64" r="54" fill="none" stroke="#e8a0a4" stroke-width="1"/><circle cx="64" cy="64" r="22" fill="none" stroke="var(--red)" stroke-width="3"/><circle cx="64" cy="58" r="6" fill="var(--red)"/><path d="M53 74a11 9 0 0 1 22 0z" fill="var(--red)"/><g fill="var(--red)"><circle cx="64" cy="36" r="4"/><circle cx="64" cy="92" r="4"/><circle cx="38" cy="50" r="4"/><circle cx="90" cy="50" r="4"/><circle cx="38" cy="78" r="4"/><circle cx="90" cy="78" r="4"/></g></svg>
    <div class="service-label">Employee<br>Experience</div>
  </div>
  <div class="service" style="left:614px;top:346px">
    <svg width="128" height="128" viewBox="0 0 128 128"><circle cx="64" cy="64" r="62" fill="none" stroke="var(--red)" stroke-width="2"/><circle cx="64" cy="64" r="54" fill="none" stroke="#e8a0a4" stroke-width="1"/><path d="M44 60a20 20 0 0 1 34-14" fill="none" stroke="var(--red)" stroke-width="4"/><path d="M74 40l6 7-9 2z" fill="var(--red)"/><path d="M84 68a20 20 0 0 1-34 14" fill="none" stroke="var(--red)" stroke-width="4"/><path d="M54 88l-6-7 9-2z" fill="var(--red)"/><rect x="66" y="56" width="16" height="14" fill="var(--red)"/><circle cx="54" cy="66" r="7" fill="var(--red)"/></svg>
    <div class="service-label">Change<br>Management</div>
  </div>
  <div class="service" style="left:850px;top:346px">
    <svg width="128" height="128" viewBox="0 0 128 128"><circle cx="64" cy="64" r="62" fill="none" stroke="var(--red)" stroke-width="2"/><circle cx="64" cy="64" r="54" fill="none" stroke="#e8a0a4" stroke-width="1"/><rect x="40" y="42" width="48" height="34" fill="none" stroke="var(--red)" stroke-width="3"/><path d="M47 68l10-10 8 6 14-14" fill="none" stroke="var(--red)" stroke-width="3"/><path d="M64 76v12M54 92l10-4 10 4" stroke="var(--red)" stroke-width="3" fill="none"/></svg>
    <div class="service-label">Executive<br>Coaching</div>
  </div>

  <div class="btn btn-white" style="left:522px;top:611px;width:156px">Learn More</div>
</section>

<section class="founder">
  <h2 class="abs title" style="top:100px">Our Founder</h2>
  <p class="abs para" style="top:181px">Lorem ipsum dolor sit amet, consectetur adipiscing elit, sed do eiusmod tempor incidi dunt ut labore et dolore magna aliqua. Ut enim ad mainim veniam, quis nostrud exercitea tion ual lamco laboris nisi ut aliquip ex ea commodo consequat.</p>
  <div class="abs photo" role="img" aria-label="Portrait photograph of the founder in a shirt and tie"></div>
  <div class="abs founder-name">Martin Ashgrove</div>
  <div class="abs founder-role">Founder</div>
  <div class="btn btn-red" style="left:693px;top:466px;width:125px;height:39px;line-height:39px;font-size:14px">Learn More</div>
</section>

<section class="insights">
  <h2 class="abs title" style="top:120px">Our Insights</h2>
  <p class="abs para" style="top:206px">Lorem ipsum dolor sit amet, consectetur adipiscing elit, sed do eiusmod tempor incidi dunt ut labore et dolore magna aliqua. Ut enim ad mainim veniam, quis nostrud exercitea tion ual lamco laboris nisi ut aliquip ex ea commodo consequat.</p>
  <div class="btn btn-white" style="left:522px;top:356px;width:156px">Learn More</div>
</section>

<section class="contact">
  <h2 class="abs title" style="top:88px">Contact Bluefinch</h2>
  <p class="abs para" style="top:162px">Ut labore et dolore magna aliqua. Ut enim ad mainim veniam, quis nostrud exercitea tion ual lamco laboris nisi ut aliquip ex ea commodo consequat.</p>

  <div class="detail" style="left:144px;top:270px">
    <svg width="34" height="34" viewBox="0 0 34 34"><circle cx="17" cy="17" r="15" fill="none" stroke="var(--red)" stroke-width="2"/><path d="M17 25s-6-6-6-10a6 6 0 0 1 12 0c0 4-6 10-6 10z" fill="var(--red)"/><circle cx="17" cy="15" r="2" fill="#fff"/></svg>
    <span>41 Linden Hill Road, ELMVALE,<br>CT 06900, U. S. A.</span>
  </div>
  <div class="detail" style="left:440px;top:270px">
    <svg width="34" height="34" viewBox="0 0 34 34"><circle cx="17" cy="17" r="15" fill="none" stroke="var(--red)" stroke-width="2"/><rect x="10" y="12" width="14" height="10" fill="var(--red)"/><path d="M10 12l7 6 7-6" fill="none" stroke="#fff" stroke-width="1.5"/></svg>
    <span style="line-height:34px">hello@bluefinchadvisorypartners.com</span>
  </div>
  <div class="detail" style="left:907px;top:270px">
    <svg width="34" height="34" viewBox="0 0 34 34"><circle cx="17" cy="17" r="15" fill="none" stroke="var(--red)" stroke-width="2"/><path d="M12 10l4 0 1 5-2 1a9 9 0 0 0 4 4l1-2 5 1 0 4c-8 1-14-5-13-13z" fill="var(--red)"/></svg>
    <span style="line-height:34px">1-555-210-7386</span>
  </div>

  <div class="btn btn-red" style="left:515px;top:373px;width:170px">Get In Touch</div>
</section>

<footer class="abs footer" style="left:0;width:1200px">
  <nav class="abs foot-nav"><span>Home</span><span>The Way We Work</span><span>What We Do</span><span>Our Founder</span><span>Insights</span><span>Contact</span></nav>
  <div class="abs copy">Copyright © 2018 &nbsp;All Rights Reserved</div>
</footer>

</body>
</html>
```